Corporate Design für eine Veranstaltungsagentur
Vielen Dank an Bartholomä, der trotz vieler unserer Revisionswünsche stets freundlich war, professionell und schnell gearbeitet hat und uns am Ende ein wirklich wunderbares Ergebnis geliefert hat! :-) Wir können ihn uneingeschränkt weiterempfehlen!
Zielgruppe
Agentur zur Planung, Organisation und Durchführung von Veranstaltungen aller Art
Ingenieurbetrieb für Veranstaltungstechnik und - produktion
Organisation und Durchführung der 'Wellenklang'-Veranstaltungsreihe: www.wellenklang-turnier.de
Zielgruppe:
Personen jeder Altersgruppe, Privatpersonen, Geschäftskunden
Aufgabenstellung
Die Farbe Grün sollte beibehalten werden.
Logo soll Professionalität und Innovation ausstrahlen, gleichzeitig modern und zeitlos wirken.

```html
<!DOCTYPE html>
<html lang="de">
<head>
<meta charset="utf-8">
<title>Verano Events – Geschäftsausstattung</title>
<link rel="stylesheet" href="https://fonts.googleapis.com/css2?family=Exo+2:wght@400;600;700&family=Arimo:wght@400;700&display=swap">
<style>
:root{
  --stage:#e9e9e7;
  --paper:#ffffff;
  --ink:#2b2b2b;
  --ink-soft:#4a4a4a;
  --green:#7cb63a;
  --green-dark:#3f9c3a;
  --card-dark:#343434;
  --rule:#c9c9c9;
}
*{margin:0;padding:0;box-sizing:border-box}
html,body{width:1200px;height:856px;overflow:hidden;background:var(--stage)}
.canvas{position:relative;width:1200px;height:856px}
.sheet,.card{position:absolute;background:var(--paper);box-shadow:0 6px 18px rgba(0,0,0,.18)}
.logo{position:absolute;text-align:center;font-family:"Exo 2",sans-serif;font-weight:600;color:var(--ink-soft);line-height:.92}
.logo-dot{display:block;margin:0 auto 4px;border-radius:50%;background:var(--green)}

/* Letterhead */
.letterhead{left:78px;top:73px;width:503px;height:711px;font-family:Arimo,sans-serif;color:var(--ink)}
.letterhead .logo{left:395px;top:32px;width:78px;font-size:19px}
.letterhead .logo-dot{width:26px;height:26px}
.sender-line{position:absolute;left:53px;top:107px;width:152px;font-family:"Exo 2",sans-serif;font-size:5.2px;color:var(--green);padding-bottom:2px;border-bottom:.8px solid var(--green);white-space:nowrap}
.recipient{position:absolute;left:53px;top:128px;font-size:8.2px;line-height:10.5px}
.recipient .city{margin-top:10px}
.salutation{position:absolute;left:53px;top:242px;font-family:"Exo 2",sans-serif;font-weight:700;font-size:8px}
.body-copy{position:absolute;left:53px;top:270px;width:276px;font-family:"Exo 2",sans-serif;font-size:7.9px;line-height:9.2px;color:var(--ink-soft)}
.body-copy p+p{margin-top:9px}
.closing{position:absolute;left:53px;top:502px;font-family:"Exo 2",sans-serif;font-size:7.9px;color:var(--ink-soft)}
.signature{position:absolute;left:53px;top:520px;width:106px;height:22px;border-radius:3px;background:linear-gradient(90deg,#e4e4e4,#f2f2f2)}
.signer{position:absolute;left:53px;top:551px;font-family:"Exo 2",sans-serif;font-size:7.9px;color:var(--ink-soft)}
.company-info{position:absolute;right:35px;top:524px;text-align:right;font-family:"Exo 2",sans-serif;font-size:5.3px;line-height:7.4px;color:var(--ink)}
.company-info p{margin-bottom:3.5px}
.company-info .accent{color:var(--green)}

/* Business cards */
.card{top:273px;width:199px;height:306px;font-family:"Exo 2",sans-serif;text-align:center}
.card-front{left:650px}
.card-front .logo{left:0;right:0;top:32px;font-size:23px}
.card-front .logo-dot{width:32px;height:32px}
.card-rule{position:absolute;left:32px;right:34px;top:138px;border-top:1.4px solid var(--rule)}
.card-details{position:absolute;left:0;right:0;top:160px;font-size:8.8px;line-height:11.3px;color:var(--ink)}
.card-details .name{font-weight:700}
.card-details .role{color:var(--green)}
.card-details .gap{margin-top:7px}
.card-details .web{margin-top:7px;font-weight:700;color:var(--green)}
.card-back{left:905px;background:var(--card-dark)}
.card-back .logo{left:0;right:0;top:104px;font-size:24px;color:#ffffff}
.card-back .logo-dot{width:34px;height:34px}
</style>
</head>
<body>
<main class="canvas">

  <article class="sheet letterhead">
    <div class="logo"><span class="logo-dot"></span>verano<br>events</div>
    <div class="sender-line">Vorname Nachname, Musterstr. 123, 12345 Musterstadt</div>
    <address class="recipient" style="font-style:normal">
      Helena Brandt<br>Lindenweg 45
      <div class="city">10117 Berlin</div>
    </address>
    <div class="salutation">Quidero molore, atatur sae. Nequat,</div>
    <div class="body-copy">
      <p>Ur sit, imus, ipicatem voluptate eum re dolluptios sequosam, eum reritati am volor sapedissi quo blaboribust, sequass itasped igendi cus exerfer fe-ruptas iusanda ndaest, qui omnis nus aut fugitinis quatur ad ullaut mostem quasperiae corem et aciatem illatin ciduntores quidis utemquam autem-perae soluptiae lab illacescia solorum et fugiam ratatatus exerro blaciis samusam etur? Uga. Neque nam simi, nest, ommod essedios magnatia nossi aute nonsequam fugiaspis moluptas sed el int etur saepe nonseca-tem excea noneceperrum ulligendit faccullores et lantur si ium at.Ota cuptae non ea de opta voles rem rae dolore ilia vellab isi blanis idit veribus auda alit labore desenis imenis que in con rehent, explat ped que volorum, autent, si tetur?</p>
      <p>Ihil ium restior ecepero reptistius es aborepe diatiunt dignis diciae voluptu ribearit, que nat aute et as maximus, qui blab iur aut volest, nonsequae odios doluptatiae velignimin peresecia vent.<br>Pa voluptas expero corectur molest eaquid enda vidus verciis quodi te dit aliquid unturem poreper feratur? Quis aut rehenihilit et quam, eris et per-orru mquamusa quo et untia volupie nisimoluptae esseribus cora doluptati doluptatur atsciumqui re pa quat aut lam solescia intiis et millabor sit odis et quos re sam, vendicientur abo. Equi totatus rest, nosam quodi omni doloriosam des ea nimpelique volo elendae dellign ihilitis solupta temporp orupta iuntia ipiste natibusapis volesedis reriori taerrup tatiberes nobitiur, sequi omnihillab id maximagnat omnimus dolo quunt, int aut earum lacit peliquunt iduciet, id que automolum deruptati te non re.</p>
    </div>
    <div class="closing">Sincerely</div>
    <div class="signature" role="img" aria-label="Handschriftliche Unterschrift"></div>
    <div class="signer">Paul Kessler</div>
    <div class="company-info">
      <p class="accent">Verano Events UG<br>(haftungsbeschränkt)</p>
      <p>Südwall 8<br>45711 Brückenfeld</p>
      <p>T: (02 41) 552 18 30<br>F: (02 41) 552 18 31<br>kontakt@verano-events.de</p>
      <p>Geschäftsführer:<br>Jonas Terbeck</p>
      <p>Sitz der Gesellschaft:<br>Brückenfeld</p>
      <p>Eingetragen beim<br>Amtsgericht Lindhagen<br>HR B 41 52</p>
      <p>USt.-Id.-Nr. DE 317 604 285</p>
      <p>Kreisbank Lindhagen<br>IBAN DE48300500000012345678<br>BIC KRBLDE33XXX</p>
      <p class="accent">www.verano-events.de</p>
    </div>
  </article>

  <section class="card card-front">
    <div class="logo"><span class="logo-dot"></span>verano<br>events</div>
    <div class="card-rule"></div>
    <div class="card-details">
      <div class="name">Vorname Nachname</div>
      <div class="role">Geschäftsführung</div>
      <div class="gap">Musterstr. 123<br>12345 Musterstadt</div>
      <div class="gap">T: 030 / 987 654 321<br>F: 030 / 987 654 322<br>info@beispielnetz.de</div>
      <div class="web">www.beispielnetz.de</div>
    </div>
  </section>

  <section class="card card-back">
    <div class="logo"><span class="logo-dot"></span>verano<br>events</div>
  </section>

</main>
</body>
</html>
```